Bramble Hockey Academy

We are are Ice Hockey Development Company that provided on-ice Hockey development services. We need a Landing Page with tabs to direct to individual program pages.
Landing Page
About Page
Winter Program Page
Spring Program Page
Summer Program Page
Team Page
Tournament Page

Coded - Design and coding required

5+ page

```html
<!DOCTYPE html>
<html lang="en">
<head>
<meta charset="utf-8">
<title>Bramble Hockey Development</title>
<link href="https://fonts.googleapis.com/css2?family=Michroma&family=Roboto:wght@400;500;700;900&display=swap" rel="stylesheet">
<style>
:root{
  --green:#1a8a23;
  --green-dark:#0f6b17;
  --ink:#111111;
  --text:#555555;
  --muted:#8a8a8a;
  --white:#ffffff;
  --night:#0c0d0e;
  --mist:#eeeff0;
}
*{box-sizing:border-box;margin:0;padding:0}
html,body{width:1200px;height:3933px;overflow:hidden}
body{position:relative;background:var(--white);font-family:'Roboto',Arial,sans-serif;color:var(--ink)}
.abs{position:absolute}
.display{font-family:'Michroma','Roboto',sans-serif;font-weight:400;letter-spacing:1px;-webkit-text-stroke:1px currentColor;white-space:nowrap}
.hl{color:var(--green)}
.btn{position:absolute;display:flex;align-items:center;justify-content:center;background:var(--green-dark);color:var(--white);font-weight:700;text-transform:uppercase;box-shadow:4px 4px 0 -1px var(--white),5px 5px 0 0 var(--ink)}
.btn.on-white{box-shadow:4px 4px 0 0 var(--white),5px 5px 0 0 var(--ink)}
.photo{position:absolute}

/* header */
.brand{position:absolute;left:111px;top:24px;color:var(--ink);font-weight:900;line-height:1;white-space:nowrap}
.brand .b1{font-size:36px;letter-spacing:1px;display:block}
.brand .b2{font-size:14px;letter-spacing:5px;display:block;margin-top:6px}
.nav{position:absolute;top:63px;left:483px;display:flex;gap:29px;font-size:14px;font-weight:500;text-transform:uppercase}
.nav a{color:var(--ink);text-decoration:none}
.nav a.active{color:var(--green)}

/* hero */
.hero-card{position:absolute;left:111px;top:282px;width:473px;height:278px;background:rgba(255,255,255,.88);border-left:6px solid var(--green)}
.hero-card h1{position:absolute;left:30px;top:30px;font-size:30px;line-height:46px}
.hero-card p{position:absolute;left:30px;top:122px;font-size:14.5px;line-height:24px;color:#333;width:410px}
.scroll-ring{position:absolute;left:344px;top:734px;width:114px;height:114px;border-radius:50%;border:1.5px solid rgba(255,255,255,.9)}
.scroll-dot{position:absolute;left:362px;top:753px;width:76px;height:76px;border-radius:50%;background:var(--white);box-shadow:0 4px 14px rgba(0,0,0,.2);display:flex;align-items:center;justify-content:center}
.side-arrow{position:absolute;width:22px;height:40px;background:rgba(255,255,255,.9);display:flex;align-items:center;justify-content:center}

/* about */
.section-title{font-size:31px;line-height:40px}
.about-text p{font-size:14.5px;line-height:26px;color:var(--muted);width:424px;text-align:justify;margin-bottom:12px}

/* programs */
.prog-card{position:absolute;top:1692px;width:309px;height:446px;background:var(--white);box-shadow:0 6px 18px rgba(0,0,0,.18);text-align:center}
.prog-card .photo{left:9px;top:9px;width:291px;height:205px}
.prog-card h3{position:absolute;top:240px;left:0;width:100%;font-size:16px;font-weight:500;text-transform:uppercase}
.prog-card p{position:absolute;top:272px;left:20px;width:269px;font-size:14px;line-height:26px;color:var(--muted)}
.prog-card .btn{top:373px;left:97px;width:112px;height:38px;font-size:12px}

/* blog */
.blog-card{position:absolute;background:var(--white);box-shadow:0 4px 16px rgba(0,0,0,.12)}
.date{position:absolute;height:27px;background:var(--green);color:var(--white);font-size:11px;font-weight:500;display:flex;align-items:center;gap:5px;padding:0 10px}
.blog-card h4{position:absolute;font-size:17px;line-height:27px;font-weight:500;text-transform:uppercase}
.blog-card p{position:absolute;font-size:14.5px;line-height:23px;color:var(--text)}

/* testimonials */
.quote-card{position:absolute;top:3135px;width:418px;height:201px;background:var(--white);border-radius:18px;box-shadow:0 6px 22px rgba(0,0,0,.08)}
.quote-card p{position:absolute;left:80px;top:30px;width:310px;font-size:13.5px;line-height:26px;color:var(--muted)}
.quote-card h5{position:absolute;left:80px;top:143px;font-size:16px;font-weight:500}
.avatar{position:absolute;width:98px;height:98px;border-radius:50%;border:6px solid var(--white);box-shadow:0 4px 14px rgba(0,0,0,.15)}

/* footer */
.foot-col h6{font-size:16.5px;font-weight:500;color:var(--white);text-transform:uppercase;margin-bottom:18px}
.foot-col li{list-style:none;display:flex;align-items:center;gap:18px;color:var(--white);font-size:14px;height:36px}
.foot-col li i{width:12px;height:12px;border-radius:50%;background:var(--green);display:inline-block;position:relative}
.foot-col li i:after{content:"";position:absolute;left:3px;top:3.5px;width:4px;height:4px;border-top:1.5px solid #000;border-right:1.5px solid #000;transform:rotate(45deg)}
.contact-item{position:absolute;left:896px;color:var(--white);font-size:12px}
.contact-item b{display:block;font-size:14px;font-weight:500;margin-bottom:4px;padding-left:33px}
.contact-item span{display:block;padding-left:33px;line-height:18px}
.contact-item svg{position:absolute;left:0;top:0}
.bottom-bar{position:absolute;left:0;top:3881px;width:1200px;height:52px;background:var(--green);color:var(--white);font-size:13px}
.social{position:absolute;top:9px;width:34px;height:34px;border-radius:50%}
</style>
</head>
<body>

<!-- HEADER -->
<header>
  <div class="brand"><span class="b1">BRAMBLE HOCKEY</span><span class="b2">DEVELOPMENT</span></div>
  <nav class="nav">
    <a class="active" href="#">Home</a><a href="#">About</a><a href="#">Programs</a><a href="#">Team</a><a href="#">Tournament</a>
  </nav>
  <a class="btn" style="left:951px;top:44px;width:131px;height:48px;font-size:14px;text-decoration:none" href="#">Contact Us</a>
</header>

<!-- HERO -->
<section>
  <div class="photo" role="img" aria-label="Ice hockey player in teal jersey and helmet driving forward with stick in an arena" style="left:0;top:138px;width:1200px;height:680px;background:linear-gradient(110deg,#a9bcc0 0%,#7f979c 35%,#3f6a78 60%,#1f4a5c 80%,#6f8c93 100%)"></div>
  <svg class="abs" style="left:0;top:560px" width="1200" height="300" viewBox="0 0 1200 300">
    <polygon points="0,51 458,200 1200,68 1200,300 0,300" fill="#ffffff"/>
    <polygon points="0,51 458,242 458,258 0,83" fill="#1a8a23"/>
    <polygon points="458,242 1200,68 1200,79 458,258" fill="#1a8a23"/>
  </svg>
  <div class="hero-card">
    <h1 class="display">BRAMBLE HOCKEY<br><span class="hl">DEVELOPMENT</span></h1>
    <p>Lorem ipsum dolor sit amet consectetur adipiscing sed do eius incididetur adipdunt ut laborea.</p>
  </div>
  <a class="btn" style="left:145px;top:476px;width:119px;height:42px;font-size:12.5px;text-decoration:none" href="#">Get Started</a>
  <div class="side-arrow" style="left:0;top:370px"><svg width="10" height="14"><path d="M7 2 2 7 7 12" fill="none" stroke="#1a8a23" stroke-width="2"/></svg></div>
  <div class="side-arrow" style="left:1178px;top:370px"><svg width="10" height="14"><path d="M3 2 8 7 3 12" fill="none" stroke="#1a8a23" stroke-width="2"/></svg></div>
  <div class="scroll-ring"></div>
  <div class="scroll-dot"><svg width="22" height="20"><path d="M3 3 11 10 19 3M3 10 11 17 19 10" fill="none" stroke="#1a8a23" stroke-width="2.5"/></svg></div>
</section>

<!-- ABOUT -->
<section>
  <h2 class="display section-title abs" style="left:111px;top:911px">ABOUT <span class="hl">US</span></h2>
  <div class="about-text abs" style="left:111px;top:979px">
    <p>Lorem ipsum dolor sit amet, consectetur adipiscing elit, sed do eiusmod tempor incididunt ut labore et dolore magna aliqua. Ut enim ad minim veniam, quis nostrud exercitation ullamco laboris nisi ut aliquip ex ea commodo consequat.</p>
    <p>Consectetur adipiscing elit, sed do eiusmod tempor incididunt ut labore et dolore magna aliqua. Ut enim ad minim veniam, quis nostrud exercitation ullamco laboris.</p>
  </div>
  <a class="btn on-white" style="left:111px;top:1206px;width:130px;height:47px;font-size:14px;text-decoration:none" href="#">Learn More</a>
  <svg class="abs" style="left:573px;top:1203px" width="114" height="110">
    <defs><pattern id="dots" width="6" height="6" patternUnits="userSpaceOnUse"><circle cx="2" cy="2" r="1" fill="#bdbdbd"/></pattern></defs>
    <rect width="114" height="110" fill="url(#dots)"/>
  </svg>
  <div class="abs" style="left:646px;top:867px;width:442px;height:378px;border:4px solid var(--green);border-left:none;border-bottom:none"></div>
  <div class="abs" style="left:1084px;top:867px;width:4px;height:378px;background:var(--green)"></div>
  <div class="photo" role="img" aria-label="Youth hockey team in red jerseys lined up on the ice with sticks" style="left:618px;top:893px;width:445px;height:377px;background:linear-gradient(180deg,#6f7d90 0%,#a33a3c 45%,#c9cfd6 100%)"></div>
</section>

<!-- PROGRAMS -->
<section>
  <svg class="abs" style="left:0;top:1305px" width="1200" height="700" viewBox="0 0 1200 700">
    <defs><linearGradient id="night" x1="0" y1="0" x2="1" y2="1"><stop offset="0" stop-color="#1e2124"/><stop offset="1" stop-color="#0a0b0c"/></linearGradient></defs>
    <polygon points="0,8 1200,8 1200,590 0,683" fill="url(#night)"/>
    <polygon points="800,170 1200,0 1200,8 800,180" fill="#1a8a23"/>
    <polygon points="0,8 1200,8 1200,0 800,165" fill="#ffffff"/>
    <polygon points="0,20 798,178 798,160 0,8" fill="#1a8a23"/>
    <polygon points="1089,440 1200,428 1200,665 1089,635" fill="#1a8a23"/>
  </svg>
  <h2 class="display section-title abs" style="left:0;width:1200px;text-align:center;top:1537px;color:var(--white)"><span class="hl">OUR</span> PROGRAMS</h2>
  <p class="abs" style="left:200px;width:800px;top:1597px;text-align:center;color:var(--white);font-size:13.5px;font-weight:500;line-height:25px">Lorem ipsum dolor sit amet, consectetur adipiscing elit, sed do eiusmod tempor incididunt ut labore et dolore magna ali quinim veniam, quis nostrud exercitation ullamco laborisea.</p>
  <svg class="abs" style="left:48px;top:1828px" width="16" height="24"><path d="M12 2 3 12 12 22" fill="none" stroke="#fff" stroke-width="2.5"/></svg>
  <svg class="abs" style="left:1136px;top:1828px" width="16" height="24"><path d="M4 2 13 12 4 22" fill="none" stroke="#fff" stroke-width="2.5"/></svg>

  <article class="prog-card" style="left:111px">
    <div class="photo" role="img" aria-label="Two hockey players battling for the puck on ice" style="background:linear-gradient(160deg,#4b5560,#b94747 45%,#dfe3e8)"></div>
    <h3>Winter Program</h3>
    <p>Lorem ipsum dolor sit amet, consectetur adi piscing elit, sed do eiusmod tempor inci didunt labore dolorea.</p>
    <a class="btn on-white" style="text-decoration:none" href="#">Learn More</a>
  </article>
  <article class="prog-card" style="left:446px">
    <div class="photo" role="img" aria-label="Close-up of hockey stick and skates on arena ice" style="background:linear-gradient(180deg,#26323c,#4d5864 50%,#c7ced6)"></div>
    <h3>Spring Program</h3>
    <p>Lorem ipsum dolor sit amet, consectetur adi piscing elit, sed do eiusmod tempor inci didunt labore dolorea.</p>
    <a class="btn on-white" style="text-decoration:none" href="#">Learn More</a>
  </article>
  <article class="prog-card" style="left:780px">
    <div class="photo" role="img" aria-label="Field hockey players in white celebrating on a blue turf pitch" style="background:linear-gradient(180deg,#c9a089,#d9d4cc 45%,#2f6fb5 80%,#2b8a4a)"></div>
    <h3>Summer Program</h3>
    <p>Lorem ipsum dolor sit amet, consectetur adi piscing elit, sed do eiusmod tempor inci didunt labore dolorea.</p>
    <a class="btn on-white" style="text-decoration:none" href="#">Learn More</a>
  </article>
</section>

<!-- BLOG -->
<section>
  <h2 class="display section-title abs" style="left:0;width:1200px;text-align:center;top:2240px">LATEST <span class="hl">BLOG</span></h2>

  <article class="blog-card" style="left:111px;top:2324px;width:480px;height:429px">
    <div class="photo" role="img" aria-label="Goalie in orange making a save in front of the net" style="left:7px;top:7px;width:466px;height:258px;background:linear-gradient(135deg,#d7dadd,#e56a2c 40%,#f1f2f3 70%,#b9bec3)"></div>
    <div class="date" style="left:41px;top:258px"><svg width="10" height="10"><rect x="0.5" y="1.5" width="9" height="8" fill="none" stroke="#fff"/><line x1="0" y1="4" x2="10" y2="4" stroke="#fff"/></svg>22 Mar 2023</div>
    <h4 style="left:40px;top:304px;width:420px">Lorem ipsum dolor sit amet, consec tet adipiscing elitm dolo</h4>
    <p style="left:40px;top:366px;width:390px">Sed ut perspiciatis unde omnis iste natus error sit vol up tatem accusants iste natus erroque.</p>
  </article>

  <article class="blog-card" style="left:609px;top:2324px;width:480px;height:200px">
    <div class="photo" role="img" aria-label="Field hockey player in yellow dribbling the ball" style="left:7px;top:7px;width:179px;height:186px;background:linear-gradient(180deg,#3d6f3a,#c9e23c 45%,#5f8f54)"></div>
    <div class="date" style="left:213px;top:22px"><svg width="10" height="10"><rect x="0.5" y="1.5" width="9" height="8" fill="none" stroke="#fff"/><line x1="0" y1="4" x2="10" y2="4" stroke="#fff"/></svg>22 Mar 2023</div>
    <h4 style="left:213px;top:73px;width:250px">Lorem ipsum dolor sit am consec tetur adipi</h4>
    <p style="left:213px;top:136px;width:250px">Sed ut perspiciatis unde omnis iste natus error sit vol</p>
  </article>

  <article class="blog-card" style="left:609px;top:2553px;width:480px;height:200px">
    <div class="photo" role="img" aria-label="Youth hockey players contesting on the ice" style="left:7px;top:7px;width:179px;height:186px;background:linear-gradient(180deg,#8a8f96,#b9393b 40%,#e8eaee)"></div>
    <div class="date" style="left:213px;top:22px"><svg width="10" height="10"><rect x="0.5" y="1.5" width="9" height="8" fill="none" stroke="#fff"/><line x1="0" y1="4" x2="10" y2="4" stroke="#fff"/></svg>22 Mar 2023</div>
    <h4 style="left:213px;top:73px;width:250px">Lorem ipsum dolor sit am consec tetur adipi</h4>
    <p style="left:213px;top:136px;width:250px">Sed ut perspiciatis unde omnis iste natus error sit vol</p>
  </article>
</section>

<!-- TESTIMONIALS -->
<section>
  <svg class="abs" style="left:0;top:2790px" width="1200" height="640" viewBox="0 0 1200 640">
    <defs><linearGradient id="mist" x1="0" y1="0" x2="1" y2="1"><stop offset="0" stop-color="#f4f4f5"/><stop offset="1" stop-color="#e7e8ea"/></linearGradient></defs>
    <rect x="0" y="0" width="1200" height="640" fill="url(#mist)"/>
    <polygon points="0,0 1200,0 1200,18 402,175 0,5" fill="#ffffff"/>
    <polygon points="0,5 402,155 402,160 0,13" fill="#1a8a23"/>
    <polygon points="402,180 1200,15 1200,20 402,200" fill="#1a8a23"/>
  </svg>
  <h2 class="display section-title abs" style="left:0;width:1200px;text-align:center;top:3043px">TESTIMONIALS</h2>
  <svg class="abs" style="left:44px;top:3220px" width="18" height="30"><path d="M15 2 3 15 15 28" fill="none" stroke="#9a9a9a" stroke-width="3"/></svg>
  <svg class="abs" style="left:1138px;top:3220px" width="18" height="30"><path d="M3 2 15 15 3 28" fill="none" stroke="#9a9a9a" stroke-width="3"/></svg>

  <div class="quote-card" style="left:168px">
    <p>Lorem ipsum dolor sit amet, consectetur adipisc ing elit, sed do eiusmod tempor incididunt ut labo re et dolore magna aliqua ut enim ad minim veni am, quis nostrud exercita.</p>
    <h5>JORDAN REYES</h5>
    <svg class="abs" style="left:80px;top:166px" width="70" height="12"><g fill="#1a8a23"><path id="st" d="M6 0 7.6 4.2 12 4.4 8.6 7.2 9.7 11.5 6 9 2.3 11.5 3.4 7.2 0 4.4 4.4 4.2Z"/><use href="#st" x="14"/><use href="#st" x="28"/><use href="#st" x="42"/><use href="#st" x="56"/></g></svg>
  </div>
  <div class="avatar" role="img" aria-label="Portrait of a smiling older man" style="left:116px;top:3185px;background:linear-gradient(180deg,#c9cdd2,#8aa5c2)"></div>

  <div class="quote-card" style="left:670px">
    <p>Lorem ipsum dolor sit amet, consectetur adipisc ing elit, sed do eiusmod tempor incididunt ut labo re et dolore magna aliqua ut enim ad minim veni am, quis nostrud exercita.</p>
    <h5>JORDAN REYES</h5>
    <svg class="abs" style="left:80px;top:166px" width="70" height="12"><g fill="#1a8a23"><use href="#st"/><use href="#st" x="14"/><use href="#st" x="28"/><use href="#st" x="42"/><use href="#st" x="56"/></g></svg>
  </div>
  <div class="avatar" role="img" aria-label="Portrait of a smiling young woman" style="left:617px;top:3185px;background:linear-gradient(180deg,#e2e2e2,#5a4238)"></div>
</section>

<!-- FOOTER -->
<footer>
  <svg class="abs" style="left:0;top:3385px" width="1200" height="500" viewBox="0 0 1200 500">
    <polygon points="0,5 1200,178 1200,500 0,500" fill="#1a8a23"/>
    <polygon points="0,240 1200,110 1200,500 0,500" fill="#000000"/>
    <polygon points="0,240 1200,110 1200,178" fill="#1a8a23"/>
  </svg>
  <div class="brand" style="top:3700px;color:var(--white)"><span class="b1" style="font-size:32px">BRAMBLE HOCKEY</span><span class="b2" style="font-size:14px">DEVELOPMENT</span></div>

  <div class="foot-col abs" style="left:475px;top:3641px">
    <h6>Navigation</h6>
    <ul><li><i></i>Home</li><li><i></i>About</li><li><i></i>Programs</li><li><i></i>Team</li><li><i></i>Tournament</li></ul>
  </div>
  <div class="foot-col abs" style="left:675px;top:3641px">
    <h6>Quick Links</h6>
    <ul><li><i></i>Privacy Policy</li><li><i></i>Terms Of Use</li><li><i></i>Legal Support</li></ul>
  </div>
  <div class="foot-col abs" style="left:896px;top:3641px"><h6>Contact Info</h6></div>
  <div class="contact-item" style="top:3689px">
    <svg width="12" height="14"><path d="M6 0C2.7 0 0 2.6 0 5.8 0 10 6 14 6 14S12 10 12 5.8C12 2.6 9.3 0 6 0Z" fill="#1a8a23"/><circle cx="6" cy="5.6" r="2" fill="#000"/></svg>
    <b>ADDRESS:</b><span>465, Lorum Ipsum Dolore Sed,<br>United States</span>
  </div>
  <div class="contact-item" style="top:3769px">
    <svg width="13" height="13"><path d="M2.6 0 5 2.9 3.6 4.6C4.5 6.5 6.4 8.5 8.4 9.4L10.1 8 13 10.4 11.3 13C5.4 12.6.4 7.6 0 1.7Z" fill="#1a8a23"/></svg>
    <b>PHONE:</b><span>+1 (888) 888 8888</span>
  </div>
  <div class="contact-item" style="top:3823px">
    <svg width="14" height="11"><rect width="14" height="11" fill="#1a8a23"/><path d="M0 0 7 6 14 0" fill="none" stroke="#000" stroke-width="1.3"/></svg>
    <b>EMAIL:</b><span>info@bramblehockey.com</span>
  </div>

  <div class="bottom-bar">
    <p class="abs" style="left:0;width:1200px;top:17px;text-align:center">© 2023 <b style="font-weight:700">BRAMBLE HOCKEY DEVELOPMENT</b> &nbsp;/&nbsp; All Rights Reserved</p>
    <span class="social" aria-label="Social profile one" style="left:938px;background:var(--white)"></span>
    <span class="social" aria-label="Social profile two" style="left:976px;background:rgba(255,255,255,.35)"></span>
    <span class="social" aria-label="Social profile three" style="left:1015px;background:rgba(255,255,255,.35)"></span>
    <span class="social" aria-label="Social profile four" style="left:1055px;background:rgba(255,255,255,.35)"></span>
  </div>
</footer>

</body>
</html>
```